BrivoTerna. Lantern of the Steady Harvest. Business card

Professional business card for BrivoTerna (Lantern of the Steady Harvest)
My rationale: Strategy-> Execution-> Results-> Value that lead to the BrivoTerna name: We put the Lantern of the Steady Harvest.
We deliver value to our customers helping them at defining a good strategy (cyan arrow). 90% of well formulated strategies fail due to poor execution so we also consider strategical execution very important (green arrow). Due to the execution we obtain the results (blue arrow). Finally, the results provide feedback to redefine strategy, and the new strategy has to be executed and new results obtained providing new feedback and on and on. It's like a wheel that finally, must create corporate value: value for shareholders, staholders, employees, providers...-

Target Market(s)

CEOs and steering comitees , invewrnent funds

Industry/Entity Type

Business Consultant

Contact Information for Business Card

Teodoro Vinsquel
CEO & Founder
teodoro.vinsquel@brivoterna-example.com
Mobile: +34 655.803.912
www.brivoterna-example.com

Colors

Designer to choose colors to be used in the design.

Requirements
Nice to have
• Nice to hace the words: Strategy, execution, results
• Nice to vave the claim: Lantern of the Steady Harvest
• The three colors should be shown:
• cyan for STRATEGY
• green for EXECUTION
• blue for RESULTS
Should not have
• Complete black background

```html
<!DOCTYPE html>
<html lang="en">
<head>
<meta charset="utf-8">
<title>BrivoTerna — Business Card</title>
<link href="https://fonts.googleapis.com/css2?family=Arimo:wght@400;700&display=swap" rel="stylesheet">
<style>
  :root {
    --backdrop: #5a5c62;
    --navy: #2e3192;
    --cyan: #29abe2;
    --green: #8dc63f;
    --band: #141414;
    --paper: #ffffff;
    --ink: #1d1d1f;
  }
  * { margin: 0; padding: 0; box-sizing: border-box; }
  html, body {
    width: 1200px;
    height: 766px;
    overflow: hidden;
    background: var(--backdrop);
    font-family: "Arimo", Arial, sans-serif;
  }
  .sheet {
    width: 1200px;
    height: 766px;
    display: flex;
    align-items: center;
    justify-content: center;
    gap: 40px;
  }
  .card {
    position: relative;
    width: 540px;
    height: 309px;
    overflow: hidden;
    box-shadow: 0 14px 30px rgba(0,0,0,0.35);
  }
  .card-band {
    position: absolute;
    left: 0; right: 0; bottom: 0;
    height: 44px;
    background: var(--band);
    display: flex;
    align-items: center;
  }

  /* Front */
  .card--front { background: var(--paper); }
  .front-brand {
    position: absolute;
    left: 40px;
    top: 0;
    height: 265px;
    width: 170px;
    display: flex;
    align-items: center;
    justify-content: center;
  }
  .brand-name {
    font-weight: 700;
    font-size: 30px;
    letter-spacing: -0.5px;
    color: var(--navy);
  }
  .front-divider {
    position: absolute;
    left: 222px;
    top: 70px;
    width: 2px;
    height: 125px;
    background: var(--green);
  }
  .contact {
    position: absolute;
    left: 244px;
    top: 62px;
    color: var(--ink);
  }
  .contact-name {
    font-weight: 700;
    font-size: 21px;
    color: var(--navy);
    line-height: 1.1;
  }
  .contact-name .surname { color: var(--cyan); }
  .contact-role {
    font-size: 13px;
    margin-top: 4px;
    margin-bottom: 16px;
  }
  .contact-list { list-style: none; }
  .contact-item {
    display: flex;
    align-items: center;
    gap: 8px;
    font-size: 11.5px;
    line-height: 1;
    margin-bottom: 7px;
  }
  .contact-item svg { width: 11px; height: 11px; flex: none; }
  .tagline {
    padding-left: 40px;
    font-weight: 700;
    font-size: 13px;
    letter-spacing: 0.6px;
    display: flex;
    gap: 8px;
  }
  .tagline .strategy { color: var(--cyan); }
  .tagline .execution { color: var(--green); }
  .tagline .results { color: var(--navy); }

  /* Back */
  .card--back { background: var(--navy); }
  .back-brand {
    position: absolute;
    left: 0; right: 0; top: 0;
    height: 265px;
    display: flex;
    align-items: center;
    justify-content: center;
  }
  .back-brand .brand-name {
    color: #ffffff;
    font-size: 52px;
  }
  .claim {
    width: 100%;
    text-align: center;
    font-weight: 700;
    font-size: 13px;
    letter-spacing: 0.5px;
    color: var(--cyan);
    text-transform: uppercase;
  }
</style>
</head>
<body>
  <main class="sheet">
    <section class="card card--front" aria-label="Business card front">
      <div class="front-brand">
        <span class="brand-name">BrivoTerna</span>
      </div>
      <div class="front-divider"></div>
      <div class="contact">
        <p class="contact-name">Teodoro <span class="surname">Vinsquel</span></p>
        <p class="contact-role">CEO &amp; Founder</p>
        <ul class="contact-list">
          <li class="contact-item">
            <svg viewBox="0 0 12 12" aria-hidden="true"><rect x="1" y="1.5" width="10" height="9" fill="none" stroke="#2e3192" stroke-width="1.3"/></svg>
            <span>+34 655.803.912</span>
          </li>
          <li class="contact-item">
            <svg viewBox="0 0 12 12" aria-hidden="true"><rect x="0.5" y="2" width="11" height="8" fill="#2e3192"/><path d="M0.5 2 L6 7 L11.5 2" fill="none" stroke="#fff" stroke-width="1"/></svg>
            <span>teodoro.vinsquel@brivoterna-example.com</span>
          </li>
          <li class="contact-item">
            <svg viewBox="0 0 12 12" aria-hidden="true"><circle cx="6" cy="6" r="5.2" fill="#2e3192"/><path d="M1 6 H11 M6 1 V11 M6 1 C3 4 3 8 6 11 M6 1 C9 4 9 8 6 11" fill="none" stroke="#fff" stroke-width="0.7"/></svg>
            <span>www.brivoterna-example.com</span>
          </li>
        </ul>
      </div>
      <div class="card-band">
        <p class="tagline">
          <span class="strategy">• STRATEGY</span>
          <span class="execution">• EXECUTION</span>
          <span class="results">• RESULTS</span>
        </p>
      </div>
    </section>

    <section class="card card--back" aria-label="Business card back">
      <div class="back-brand">
        <span class="brand-name">BrivoTerna</span>
      </div>
      <div class="card-band">
        <p class="claim">Lantern of the Steady Harvest</p>
      </div>
    </section>
  </main>
</body>
</html>
```